Business Card Design Project - 2 sided

We need a business card design for a card having one business on each side (ie. two businesses on one card). Would like a design that incorporates logo, tagline and normal fields (name, position, address, phone).

Would also like an allowance for small font text along the bottom (text to be determined, but less than 50 characters).

NB. Attached logo for Harbor Quill has two variations - either can be used.

www.harborquill-example.com / www.velmaro-example.com

```html
<!DOCTYPE html>
<html lang="en">
<head>
<meta charset="utf-8">
<title>Two-business card – Harbor Quill / Velmaro</title>
<link href="https://fonts.googleapis.com/css2?family=Open+Sans:wght@400;600;700&family=Cinzel:wght@500&display=swap" rel="stylesheet">
<style>
  :root{
    --page:#ece8e3;
    --card-white:#ffffff;
    --navy:#29235f;
    --divider:#7ab648;
    --blue-light:#86bbda;
    --blue-deep:#1c7db3;
    --teal-text:#2a8fc0;
    --ink:#222222;
    --white:#ffffff;
  }
  *{box-sizing:border-box;margin:0;padding:0}
  html,body{width:1200px;height:402px;overflow:hidden}
  body{background:var(--page);position:relative;font-family:"Open Sans",Arial,sans-serif}

  .card{position:absolute;top:56px;width:511px;height:291px;border-radius:18px;overflow:hidden;
        background:var(--card-white);display:flex}
  .card--harbor{left:62px}
  .card--velmaro{left:620px}

  .brand-side{width:252px;height:100%;display:flex;flex-direction:column;align-items:center;justify-content:center;text-align:center}
  .divider{width:3px;height:100%;background:var(--divider)}
  .info-side{flex:1;height:100%;position:relative;color:var(--white)}
  .card--harbor .info-side{background:var(--navy)}
  .card--velmaro .info-side{background:linear-gradient(90deg,var(--blue-light),var(--blue-deep))}

  .brand-row{display:flex;align-items:center;gap:8px}
  .brand-dot{width:18px;height:18px;border-radius:50%}
  .brand-name{font-family:"Open Sans",Arial,sans-serif;font-weight:600}
  .card--harbor .brand-name{color:var(--navy);font-size:22px;letter-spacing:.5px}
  .card--harbor .brand-dot{background:var(--divider)}
  .card--velmaro .brand-name{color:var(--teal-text);font-size:26px}
  .card--velmaro .brand-dot{background:var(--teal-text)}
  .tagline{margin-top:6px;font-size:9.5px;color:var(--ink)}
  .card--velmaro .tagline{font-size:11px;color:#555;letter-spacing:.3px}

  .person{position:absolute;left:47px;top:47px;font-size:16.5px;font-weight:700}
  .person .title{font-size:13px;font-weight:400}
  .contacts{position:absolute;left:45px;top:80px;list-style:none;font-size:13px;line-height:17.5px}
  .contacts li{display:flex;align-items:center;gap:5px}
  .contacts svg{width:10px;height:10px;fill:var(--white)}
  .address{position:absolute;left:47px;top:177px;font-size:13px;line-height:17.5px}
  .fine-print{position:absolute;left:45px;top:227px;font-size:11px;line-height:15px;letter-spacing:.2px}
</style>
</head>
<body>

<section class="card card--harbor">
  <div class="brand-side">
    <div class="brand-row"><span class="brand-dot"></span><span class="brand-name">Harbor Quill</span></div>
    <p class="tagline">Website Translation and Localisation Specialist...</p>
  </div>
  <div class="divider"></div>
  <div class="info-side">
    <p class="person">Your Name <span class="title">/ Title</span></p>
    <ul class="contacts">
      <li><svg viewBox="0 0 10 10"><path d="M2 0.5 3.8 2.5 2.8 3.8Q4 6.2 6.2 7.2L7.5 6.2 9.5 8 8 9.5Q2 9 .5 2Z"/></svg>123-456-7890</li>
      <li><svg viewBox="0 0 10 10"><rect x="2.5" y="0" width="5" height="10" rx="1"/></svg>123-456-7890</li>
      <li><svg viewBox="0 0 10 10"><rect x="0" y="4" width="10" height="6" rx="1"/><rect x="2" y="0" width="6" height="3"/></svg>123-456-7890</li>
      <li><svg viewBox="0 0 10 10"><path d="M0 2h10v7H0zM0 2l5 4 5-4" stroke="#29235f" stroke-width=".8"/></svg>name@website.com</li>
      <li><svg viewBox="0 0 10 10"><circle cx="5" cy="5" r="5"/></svg>www.website.com</li>
    </ul>
    <p class="address">Complex name, Street name<br>City, State, zip code</p>
    <p class="fine-print">xxxxxxxxxxxxxxxxxxxxxxxxxx<br>xxxxxxxxxxxxxxxxxxxxxxxxxx</p>
  </div>
</section>

<section class="card card--velmaro">
  <div class="brand-side">
    <div class="brand-row"><span class="brand-dot"></span><span class="brand-name">Velmaro LLC</span></div>
    <p class="tagline">Professional SEO Services</p>
  </div>
  <div class="divider"></div>
  <div class="info-side">
    <p class="person">Your Name <span class="title">/ Title</span></p>
    <ul class="contacts">
      <li><svg viewBox="0 0 10 10"><path d="M2 0.5 3.8 2.5 2.8 3.8Q4 6.2 6.2 7.2L7.5 6.2 9.5 8 8 9.5Q2 9 .5 2Z"/></svg>123-456-7890</li>
      <li><svg viewBox="0 0 10 10"><rect x="2.5" y="0" width="5" height="10" rx="1"/></svg>123-456-7890</li>
      <li><svg viewBox="0 0 10 10"><rect x="0" y="4" width="10" height="6" rx="1"/><rect x="2" y="0" width="6" height="3"/></svg>123-456-7890</li>
      <li><svg viewBox="0 0 10 10"><path d="M0 2h10v7H0zM0 2l5 4 5-4" stroke="#5aa0cc" stroke-width=".8"/></svg>name@website.com</li>
      <li><svg viewBox="0 0 10 10"><circle cx="5" cy="5" r="5"/></svg>www.website.com</li>
    </ul>
    <p class="address">Complex name, Street name<br>City, State, zip code</p>
    <p class="fine-print">xxxxxxxxxxxxxxxxxxxxxxxxxx<br>xxxxxxxxxxxxxxxxxxxxxxxxxx</p>
  </div>
</section>

</body>
</html>
```